Canadian company needs a packaging design for a new product line of TubGlow Hot Tub & Bath Fragran

We are looking for a packaging design for a new company based in Edmonton, Alberta Canada called TubGlow. We are developing a new product line of liquid and crystal Hot Tub & Bath Fragrances (aromatherapy) for example Lavender will be one of our fragrances. We are looking at the possibilities of using a stand up pouch and or the standard plastic bottles for our fragrance line. There will be different sizes from 150 grams to 600 grams in the crystal and 275 ml in the liquid. We would like to see bright multi-colored designs possibly with picture of the fragrance or a theme like favorite drinks or a more sensual idea. Each one of our fragrances will be a different color the main design needs to be able to have a different color of liquid or crystal in the bottle and possibly parts of the label will change colors for each fragrance. I have attached samples of another brand that we want to improve on.

Target Market(s)

Most of these fragrance are bought by women 70% men 30%
age 25 - 55

Industry/Entity Type

It Company

Requirements
Must have
• bottle size
Fragrance name
Nice to have
• Using the files below I like the circle of colors and possibly it could be made using water drops like in the file and possibly the two "S" could be designed like the third file I just added

Files

```html
<!DOCTYPE html>
<html lang="en">
<head>
<meta charset="utf-8">
<title>TubGlow Lavender Label</title>
<link rel="stylesheet" href="https://fonts.googleapis.com/css2?family=Questrial&family=Great+Vibes&display=swap">
<style>
  :root {
    --bg: #a9abad;
    --label-top: #e9fbfd;
    --label-mid: #7fe0ea;
    --aqua: #1fc6d6;
    --teal: #19a9bd;
    --violet: #5b3fc4;
    --indigo: #3a2aa8;
    --band: #3b2fae;
    --band-edge: #8a80e0;
    --brand-blue: #2f5fc9;
    --name-cyan: #8ff0fb;
    --white: #ffffff;
  }
  * { box-sizing: border-box; margin: 0; padding: 0; }
  html, body { width: 1022px; height: 1200px; overflow: hidden; }
  body {
    background: var(--bg);
    position: relative;
    font-family: "Questrial", "Century Gothic", sans-serif;
  }
  .label {
    position: absolute;
    left: 146px;
    top: 70px;
    width: 730px;
    height: 1060px;
    border-radius: 22px;
    overflow: hidden;
    background: radial-gradient(circle at 70% 12%, var(--white) 0%, var(--label-top) 25%, var(--label-mid) 60%, var(--teal) 100%);
  }
  .brand-mark {
    position: absolute;
    top: 125px;
    left: 0;
    width: 100%;
    display: flex;
    justify-content: center;
    align-items: center;
    gap: 16px;
    color: var(--brand-blue);
    font-size: 44px;
    letter-spacing: 1px;
  }
  .brand-mark .dot {
    width: 22px; height: 22px; border-radius: 50%;
    background: var(--brand-blue);
  }
  .floral-art {
    position: absolute;
    left: 0; top: 420px;
    width: 100%; height: 640px;
    background:
      radial-gradient(ellipse at 48% 42%, #b8f6fb 0%, var(--aqua) 28%, transparent 55%),
      linear-gradient(160deg, #6fd5e4 0%, var(--teal) 35%, var(--violet) 75%, var(--indigo) 100%);
  }
  .swoosh {
    position: absolute;
    left: 0; top: 420px;
    width: 730px; height: 640px;
  }
  .band {
    position: absolute;
    left: 0; top: 346px;
    width: 1022px; height: 142px;
    background: var(--band);
    border-top: 4px solid var(--band-edge);
    border-bottom: 4px solid var(--band-edge);
  }
  .product-name {
    position: absolute;
    top: 372px;
    left: 0; width: 1022px;
    text-align: center;
    color: var(--name-cyan);
    font-size: 64px;
    line-height: 1;
  }
  .fragrance-name {
    position: absolute;
    top: 470px;
    left: 146px; width: 730px;
    text-align: center;
    font-family: "Great Vibes", cursive;
    font-size: 112px;
    line-height: 1;
    color: var(--white);
    text-shadow: 0 0 3px var(--indigo), 0 0 1px var(--indigo);
  }
  .volume {
    position: absolute;
    right: 36px;
    top: 968px;
    text-align: left;
    color: var(--white);
  }
  .volume .size { font-size: 46px; line-height: 1; font-family: Arial, Helvetica, sans-serif; }
  .volume .weight { font-size: 19px; margin-top: 6px; font-family: Arial, Helvetica, sans-serif; }
</style>
</head>
<body>
  <div class="label">
    <div class="brand-mark"><span class="dot"></span><span>TubGlow</span></div>
    <div class="floral-art" role="img" aria-label="Illustration of a glowing aqua flower over soft blue and violet light bokeh"></div>
    <svg class="swoosh" viewBox="0 0 730 640" aria-hidden="true">
      <path d="M170 640 C 380 560, 600 470, 730 260 L730 640 Z" fill="var(--indigo)" opacity="0.85"/>
      <path d="M150 640 C 370 560, 600 470, 730 250" fill="none" stroke="var(--white)" stroke-width="8"/>
    </svg>
    <div class="volume">
      <div class="size">300ml</div>
      <div class="weight">NET WT: 180</div>
    </div>
  </div>
  <div class="band"></div>
  <div class="product-name">TubGlow</div>
  <div class="fragrance-name">Lavender</div>
</body>
</html>
```